Valdo Capital

We need a corporate style website design for a new company based in Shenzhen's Qianhai Special Economic Development Zone, China. We provide a range of financial services to large international investment companies. Typically these companies invest over 5 million RMB. The company is part of a group that consists of NorthKilns, ValdoTrusts and ValdoEquity. Our location and gateway into Qianhai Special Economic Zone is our core advantage. We would like to see designs that Do Not use purple and orange. The website design should be similar to other websites in this family but different enough to give it a unique style (See attached website links for reference). The final design should communicate financial safety and growth. This website will act partly as a business chamber with connections to the government so we would like it to be diplomatic in style.

www.northkilns.example
www.valdotrusts.example

*Nevegation Bar
Should including Homepage, Financial Product, Team, News.
Could refer to www.valdotrusts.example

*Contact Details

Miss Lan
Address:E 728, North Block, KMO Centre, East Sector, Shenzhen Bright Science Campus
Telephone: +86 0755 63920417
Cellphone: +86 13957280316

* Social Media
Should be grouped like:
1. Weibo QRcode+ Weibo
2. Facebook, Twitter, Linkedin.

Industry/Entity Type

Investment

```html
<!DOCTYPE html>
<html lang="en">
<head>
<meta charset="utf-8">
<title>Valdo Capital</title>
<link href="https://fonts.googleapis.com/css2?family=Figtree:wght@300;400;600;700&family=Open+Sans:ital,wght@0,400;0,600;1,400&family=Ubuntu:wght@400;500&display=swap" rel="stylesheet">
<style>
:root{
  --teal:#05afcb;
  --teal-dark:#0a8ea6;
  --ink:#2e2e2e;
  --tabbar:#333333;
  --footer:#2d2d2d;
  --footer-base:#262626;
  --grey-text:#8a8a8a;
  --footer-text:#c9c9c9;
  --white:#ffffff;
}
*{margin:0;padding:0;box-sizing:border-box}
html,body{width:858px;height:1200px;overflow:hidden;background:var(--white)}
body{position:relative;font-family:"Open Sans",sans-serif;color:var(--ink)}
.abs{position:absolute}

/* hero */
.hero{left:0;top:0;width:858px;height:459px;
  background:linear-gradient(100deg,#1d3a66 0%,#27507f 30%,#3a5f86 48%,#7a6a55 62%,#b98a3e 75%,#4a4f63 90%,#26304a 100%);}
.hero-shade{left:0;top:0;width:858px;height:459px;
  background:linear-gradient(180deg,rgba(30,50,90,.55) 0%,rgba(40,70,110,.1) 45%,rgba(10,20,40,.35) 100%)}
.brand{left:80px;top:14px;display:flex;align-items:center;gap:8px;color:var(--white)}
.brand-mark{width:22px;height:22px;border:2px solid var(--teal)}
.brand-name{font-family:"Figtree",sans-serif;font-weight:400;font-size:21px;letter-spacing:.5px;line-height:1}
.brand-sub{left:140px;top:44px;color:var(--white);font-size:8.5px;letter-spacing:1.6px}
.topbar{right:78px;top:10px;color:var(--white);font-size:10.5px;display:flex;gap:14px;align-items:center}
.topbar u{font-weight:600}
.phone{display:flex;align-items:center;gap:4px;font-size:11.5px}
.nav{left:460px;top:38px;width:320px;height:28px;background:#262626;display:flex;font-size:11.5px;color:#e0e0e0}
.nav a{display:block;height:28px;line-height:28px;padding:0 14px;text-decoration:none;color:inherit}
.nav a.active{background:var(--teal);color:var(--white);width:59px;padding:0;text-align:center}
.nav a:nth-child(2){padding-left:22px}
.welcome{left:86px;top:334px;color:var(--white);font-family:"Figtree",sans-serif;line-height:1.05}
.welcome .thin{font-weight:300;font-size:34px;letter-spacing:-.5px}
.welcome .bold{font-weight:600;font-size:35px}

/* tabs */
.tabbar{left:0;top:459px;width:858px;height:30px;background:var(--tabbar)}
.tabs{left:78px;top:456px;display:flex;font-family:"Figtree",sans-serif;font-weight:600;font-size:14px;color:var(--white)}
.tabs span{height:33px;line-height:36px;padding:0 14px;border-right:1px solid #444}
.tabs span.active{background:var(--teal);width:143px;text-align:center;padding:0}
.tabs span:nth-child(2){width:97px;text-align:center;padding:0}
.tabs span:nth-child(3){width:124px;text-align:center;padding:0}

/* products */
.products{left:0;top:489px;width:858px;height:217px;background:var(--teal)}
.product{top:542px;width:200px;text-align:center;color:var(--white)}
.product svg{display:block;margin:0 auto}
.product h3{font-family:"Figtree",sans-serif;font-weight:600;font-size:14.5px;margin-top:9px;letter-spacing:-.1px}
.product p{font-family:"Ubuntu",sans-serif;font-size:9.3px;line-height:12.8px;margin-top:3px}
.arrow{top:574px}

/* about */
.about{left:91px;top:733px;width:448px}
h2.section{font-family:"Figtree",sans-serif;font-weight:400;font-size:14.5px;color:#222}
.about p{font-size:8.6px;line-height:14.3px;color:var(--grey-text);margin-top:9px}
.about p:first-of-type{margin-top:10px}
.btn-dark{left:89px;top:922px;width:68px;height:24px;background:#2c2c2c;color:var(--white);border-radius:2px;
  font-family:"Figtree",sans-serif;font-weight:600;font-size:10px;line-height:24px;text-align:center}
.testimonials{left:561px;top:733px}
.quote-box{left:562px;top:761px;width:219px;height:106px;border:1px solid #cfcfcf;background:var(--white)}
.quote-box p{position:absolute;left:18px;top:22px;width:188px;font-size:9px;line-height:14.3px;color:#555}
.qm{font-family:"Figtree",sans-serif;font-size:18px;color:#aaa;font-weight:700}
.avatar{left:564px;top:877px;width:44px;height:44px;border-radius:50%;background:linear-gradient(160deg,#d9b68a,#5a4a3e)}
.t-name{left:614px;top:884px;color:var(--teal);font-size:10px}
.t-role{left:614px;top:898px;color:#444;font-size:10px}
.view-all{left:564px;top:935px;font-style:italic;font-size:10.5px;color:#333}

/* footer */
.footer{left:0;top:967px;width:858px;height:195px;background:var(--footer)}
.f-col{top:1000px;color:var(--footer-text)}
.f-col h4{font-weight:400;font-size:11px;color:#e6e6e6;display:flex;align-items:center;gap:4px}
.f-col h4::after{content:"";display:block;height:3px;border-top:1px solid #555;border-bottom:1px solid #555;flex:1}
.f-col .lines{margin-top:18px;font-size:8.6px;line-height:14.4px}
.f-col .lines u{display:block;text-decoration:underline}
.f-col p.lines{line-height:15.8px}
.social{display:flex;gap:10px;margin-top:18px}
.social span{width:23px;height:23px;border-radius:2px;background:#3a7bbf}
.news-input{left:581px;top:1096px;width:190px;height:24px;background:var(--white);border:1px solid #ccc}
.news-input span{position:absolute;left:8px;top:6px;font-style:italic;font-size:8px;color:#555}
.news-btn{position:absolute;right:2px;top:2px;width:59px;height:18px;background:var(--teal);color:var(--white);font-size:9.5px;text-align:center;line-height:18px}
.base{left:0;top:1162px;width:858px;height:38px;background:var(--footer-base);border-top:1px solid #3a3a3a}
.base-links{left:89px;top:1175px;display:flex;gap:12px;font-size:9.2px;color:#ccc}
.copy{right:85px;top:1175px;font-size:9.2px;color:#ccc}
</style>
</head>
<body>

<div class="abs hero" role="img" aria-label="Night-time photograph of a harbour city skyline with illuminated towers and waterfront"></div>
<div class="abs hero-shade"></div>

<div class="abs brand"><span class="brand-mark"></span><span class="brand-name">Valdo Capital</span></div>
<div class="abs brand-sub">深圳前海瓦朗资本控股有限公司</div>

<div class="abs topbar">
  <span><u>EN</u> | SP ▾</span>
  <span class="phone">
    <svg width="7" height="11" viewBox="0 0 7 11"><rect x=".5" y=".5" width="6" height="10" rx="1" fill="none" stroke="#fff"/><circle cx="3.5" cy="8.6" r=".7" fill="#fff"/></svg>
    +86 0755 63920417
  </span>
</div>

<nav class="abs nav">
  <a class="active">Home</a><a>Financial Products</a><a>Teams</a><a>News</a>
</nav>

<div class="abs welcome">
  <div class="thin">Welcome To</div>
  <div class="bold">Valdo Capital</div>
</div>

<div class="abs tabbar"></div>
<div class="abs tabs"><span class="active">Financial Products</span><span>Our Blog</span><span>News &amp; Events</span></div>

<section class="abs products"></section>

<svg class="abs arrow" style="left:30px" width="20" height="44" viewBox="0 0 20 44"><path d="M18 2 L4 22 L18 42 L12 22 Z" fill="#0b8aa0"/></svg>
<svg class="abs arrow" style="left:808px" width="20" height="44" viewBox="0 0 20 44"><path d="M2 2 L16 22 L2 42 L8 22 Z" fill="#0b8aa0"/></svg>

<div class="abs product" style="left:90px">
  <svg width="66" height="42" viewBox="0 0 66 42" fill="#fff">
    <circle cx="33" cy="9" r="8"/><path d="M19 38 Q20 20 33 19 Q46 20 47 38 Z"/>
    <circle cx="16" cy="14" r="6.5"/><path d="M3 39 Q4 24 16 23 Q22 23 24 28 L20 39 Z"/>
    <circle cx="50" cy="14" r="6.5"/><path d="M63 39 Q62 24 50 23 Q44 23 42 28 L46 39 Z"/>
  </svg>
  <h3>CONSULTANCY</h3>
  <p>Lorem ipsum dolor sit amet, consectetur adipi-sicing elit, sed do eiusmod tempor incididunt ut labore et dolore.</p>
</div>

<div class="abs product" style="left:329px">
  <svg width="42" height="42" viewBox="0 0 42 42" fill="#fff">
    <text x="13" y="12" font-family="Figtree,sans-serif" font-weight="700" font-size="14">$</text>
    <rect x="3" y="30" width="5" height="10"/><rect x="11" y="26" width="5" height="14"/><rect x="19" y="28" width="5" height="12"/><rect x="27" y="20" width="5" height="20"/><rect x="35" y="14" width="5" height="26"/>
    <path d="M3 26 L14 18 L22 23 L36 8" stroke="#fff" stroke-width="2.5" fill="none"/><path d="M31 6 L39 5 L38 13 Z"/>
  </svg>
  <h3>VALDO CAPITAL</h3>
  <p>Lorem ipsum dolor sit amet, consectetur adipi-sicing elit, sed do eiusmod tempor incididunt ut labore et dolore.</p>
</div>

<div class="abs product" style="left:568px">
  <svg width="46" height="42" viewBox="0 0 46 42" fill="#fff">
    <path d="M23 1 L45 20 L40 20 L23 6 L6 20 L1 20 Z"/><rect x="33" y="4" width="5" height="9"/>
    <path d="M8 21 L23 9 L38 21 L38 41 L8 41 Z"/>
    <rect x="13" y="24" width="6" height="6" fill="#05afcb"/><rect x="27" y="24" width="6" height="6" fill="#05afcb"/><rect x="20" y="31" width="6" height="10" fill="#05afcb"/>
  </svg>
  <h3>PROPERTY MANAGEMENT</h3>
  <p>Lorem ipsum dolor sit amet, consectetur adipi-sicing elit, sed do eiusmod tempor incididunt ut labore et dolore.</p>
</div>

<section class="abs about">
  <h2 class="section">About Valdo Capital</h2>
  <p>Lorem ipsum dolor sit amet, consectetur adipisicing elit, sed do eiusmod tempor incididunt ut labore et dolore magna aliqua. Ut enim ad minim veniam, quis nostrud exercitation ullamco laboris nisi ut aliquip ex ea commodo consequat.</p>
  <p>Duis aute irure dolor in reprehenderit in voluptate velit esse cillum dolore eu fugiat nulla pariatur. Excepteur sint occaecat cupidatat non proident, sunt in culpa qui officia deserunt mollit anim id est laborum. Ut enim ad minim veniam, quis nostrud exercitation ullamco laboris nisi ut aliquip ex ea commodo consequat.</p>
  <p>Lorem ipsum dolor sit amet, consectetur adipisicing elit, sed do eiusmod tempor incididunt ut labore et dolore magna aliqua. Ut enim ad minim veniam, quis nostrud exercitation ullamco laboris nisi ut aliquip ex ea commodo consequat.</p>
</section>
<div class="abs btn-dark">Read More</div>

<h2 class="abs section testimonials">Testimonials</h2>
<div class="abs quote-box">
  <span class="abs qm" style="left:6px;top:2px">“</span>
  <p>Lorem Ipsum is simply dummy text of the printing and typesetting industry. Lorem Ipsum has been the industry's standard dummy text ever since the 1500s, when</p>
  <span class="abs qm" style="right:8px;bottom:-6px">”</span>
</div>
<svg class="abs" style="left:578px;top:866px" width="16" height="8" viewBox="0 0 16 8"><path d="M0 0 L8 7 L16 0" fill="#fff" stroke="#cfcfcf"/></svg>
<div class="abs avatar" role="img" aria-label="Portrait photo of the testimonial author"></div>
<div class="abs t-name">Mara Ellison</div>
<div class="abs t-role">Manager</div>
<div class="abs view-all">View All</div>

<footer class="abs footer"></footer>

<div class="abs f-col" style="left:88px;width:111px">
  <h4>Contact Info</h4>
  <div class="lines">
    <u>Address: E 728, North Block, KMO Centre, East Sector, Shenzhen Bright Science Campus</u>
    <u>eMail: info@valdocapital.example</u>
    <u>Telephone: +86 0755 63920417</u>
    <u>Cell: +86 13957280316</u>
  </div>
</div>

<div class="abs f-col" style="left:240px;width:151px">
  <h4>About Us</h4>
  <p class="lines">Lorem ipsum dolor sit amet, consectetur adipisicing elit, sed do eiusmod tempor incididunt ut labore et dolore magna aliqua. Ut enim ad minim veniam.</p>
</div>

<div class="abs f-col" style="left:430px;width:112px">
  <h4>Company Info</h4>
  <div class="lines"><u>Lorem ipsum</u><u>dolor sit amet</u><u>consectetur</u><u>adipisicing elit</u></div>
</div>

<div class="abs f-col" style="left:581px;width:190px">
  <h4>Stay updates on our Socail Network</h4>
  <div class="social"><span aria-label="Social network 1"></span><span aria-label="Social network 2" style="background:#4aa3df"></span><span aria-label="Social network 3" style="background:#2b78b3"></span></div>
  <h4 style="margin-top:20px">Join Our Newsletter</h4>
</div>
<div class="abs news-input"><span>Enter your email address</span><div class="news-btn">Subscribe</div></div>

<div class="abs base"></div>
<div class="abs base-links"><span>Home</span><span>Financial Products</span><span>Team</span><span>News</span></div>
<div class="abs copy">© Copyrights 2014 All rights Reserved</div>

</body>
</html>
```